Elegant Business Card for Technology Company

Client is a supplier of innovative industrial communications and automation equipment since 2002. This contest is to gather fresh ideas for a redesign of the existing business card. Client is looking for design that best communicates tagline "Industrial Networking and Computing Specialist".

Design submissions should look modern, clean, elegant and professional. It should not be cluttered. Use white as the primary colour. Orange and black as secondary colour. Refer to jpeg File 1 on the current design.

Fonts used by Client used include Arial Regular, Arial Black, Roboto Regular, Roboto Black and Lato.

The winning design will be sent for offset printing using super white 250gsm artcard paper (open for suggestions).

Target Market(s)

System Engineers, Project Managers, Purchasing Managers from companies providing engineering services for Smart Cities.

Industry/Entity Type

Information Technology

Contact Information for Business Card

Refer to PDF File 3 for Business Card Details. Priority of short contact information would be as follows Name > Job Title > Email > Mobile > Web > Tel > Fax > Business Address >UEN (UEN represents company registration number)

Font styles to use
Sans Serif

Colors
ffffff
f37122
000000
5c5c5c

Requirements
Must have
• Refer to AI File 2 (Company Logo) & PDF File 3 (Information on Namecard)
Should not have
• No QR codes
• No Social Media Icons
• Do not create full Black or Orange colour background

```html
<!DOCTYPE html>
<html lang="en">
<head>
<meta charset="utf-8">
<title>Norvex Asia Pacific – Business Card</title>
<link rel="stylesheet" href="https://fonts.googleapis.com/css2?family=Open+Sans:wght@400;600;700&display=swap">
<style>
  :root {
    --white: #ffffff;
    --orange: #f37122;
    --black: #000000;
    --ink: #141414;
    --grey: #5c5c5c;
    --backdrop: #e8e6e2;
    --font: "Open Sans", Arial, sans-serif;
  }
  * { box-sizing: border-box; margin: 0; padding: 0; }
  html, body { width: 1200px; height: 780px; overflow: hidden; }
  body { background: var(--backdrop); font-family: var(--font); position: relative; }

  .card {
    position: absolute; top: 235px; width: 540px; height: 310px;
    background: var(--white); overflow: hidden;
    box-shadow: 0 10px 28px rgba(0,0,0,.18);
  }
  .card--front { left: 40px; }
  .card--back { left: 620px; }

  .front-shape { position: absolute; inset: 0; }

  .brand { position: absolute; display: flex; align-items: center; gap: 10px; }
  .brand__dot { width: 34px; height: 34px; border-radius: 50%; background: var(--orange); }
  .brand__name { font-weight: 700; color: var(--ink); letter-spacing: 1px; }
  .card--front .brand { left: 38px; top: 168px; }
  .card--front .brand__name { font-size: 34px; }
  .card--back .brand { left: 34px; top: 28px; }
  .card--back .brand__dot { width: 26px; height: 26px; }
  .card--back .brand__name { font-size: 26px; }

  .contact { position: absolute; left: 318px; top: 22px; width: 200px; color: var(--white); }
  .contact__company { font-size: 14px; font-weight: 600; }
  .rule { height: 1px; background: rgba(255,255,255,.7); margin: 8px 0 10px; }
  .contact__name { font-size: 20px; font-weight: 700; line-height: 1.1; }
  .contact__title { font-size: 12px; color: var(--orange); margin-bottom: 10px; }
  .contact__line { display: flex; align-items: center; gap: 7px; font-size: 12px; line-height: 19px; }
  .icon { width: 12px; height: 12px; background: var(--orange); display: inline-flex; align-items: center; justify-content: center; flex: none; }
  .contact__web { font-size: 12.5px; color: var(--orange); }
  .contact__uen { font-size: 12.5px; color: var(--orange); margin-top: 4px; }
  .contact__uen b { color: var(--white); font-weight: 400; margin-left: 6px; }

  .back-company { position: absolute; right: 30px; top: 36px; font-size: 13px; color: var(--ink); }
  .tagline { position: absolute; left: 34px; top: 92px; font-size: 16px; color: var(--ink); }
  .tagline-rule { position: absolute; left: 34px; right: 30px; top: 120px; border-top: 2px dotted var(--orange); }
  .services { position: absolute; left: 34px; top: 134px; list-style: none; }
  .services li { font-size: 12.5px; color: var(--ink); line-height: 20px; display: flex; align-items: center; gap: 9px; }
  .services li::before { content: ""; width: 8px; height: 8px; border-radius: 50%; background: var(--orange); flex: none; }
  .address-band {
    position: absolute; left: 0; right: 0; bottom: 0; height: 34px; background: var(--black);
    color: var(--white); font-size: 12px; display: flex; align-items: center; padding-left: 34px;
  }
</style>
</head>
<body>

  <section class="card card--front" aria-label="Business card front">
    <svg class="front-shape" viewBox="0 0 540 310" width="540" height="310" aria-hidden="true">
      <path d="M262,0 C340,80 200,215 300,310" fill="none" stroke="#f37122" stroke-width="6" transform="translate(-8,0)"/>
      <path d="M262,0 C340,80 200,215 300,310 L540,310 L540,0 Z" fill="#000000"/>
    </svg>

    <div class="brand">
      <span class="brand__dot"></span>
      <span class="brand__name">NORVEX</span>
    </div>

    <div class="contact">
      <p class="contact__company">Norvex Asia Pacific Pte Ltd</p>
      <div class="rule"></div>
      <p class="contact__name">Daniel Lim</p>
      <p class="contact__title">Sales Manager</p>
      <p class="contact__line">
        <span class="icon"><svg width="8" height="8" viewBox="0 0 8 8"><rect x="2" y="0.5" width="4" height="7" rx="0.8" fill="#fff"/></svg></span>+65 9123 4567
      </p>
      <p class="contact__line">
        <span class="icon"><svg width="8" height="8" viewBox="0 0 8 8"><path d="M1,1 h2 l1,2 -1,1 a4,4 0 0 0 1,1 l1,-1 2,1 v2 a6,6 0 0 1 -6,-6z" fill="#fff"/></svg></span>+65 6234 5180
      </p>
      <p class="contact__line">
        <span class="icon"><svg width="8" height="8" viewBox="0 0 8 8"><rect x="1" y="3" width="6" height="4" fill="#fff"/><rect x="2" y="0.5" width="4" height="2" fill="#fff"/></svg></span>+65 6234 5191
      </p>
      <p class="contact__line">
        <span class="icon"><svg width="8" height="8" viewBox="0 0 8 8"><rect x="0.5" y="1.5" width="7" height="5" fill="#fff"/><path d="M0.5,1.5 L4,4.5 L7.5,1.5" fill="none" stroke="#f37122" stroke-width="0.8"/></svg></span>sales@norvex.example
      </p>
      <div class="rule"></div>
      <p class="contact__web">www.norvex.example</p>
      <p class="contact__uen">UEN No<b>200415736</b></p>
    </div>
  </section>

  <section class="card card--back" aria-label="Business card back">
    <div class="brand">
      <span class="brand__dot"></span>
      <span class="brand__name">NORVEX</span>
    </div>
    <p class="back-company">Norvex Asia Pacific Pte Ltd</p>
    <p class="tagline">Industrial Networking and Computing Specialist</p>
    <div class="tagline-rule"></div>
    <ul class="services">
      <li>Industrial Ethernet / Wireless / Cellular</li>
      <li>Industrial and Embedded Computing</li>
      <li>Serial / Fieldbus Connectivity</li>
      <li>IP Video Surveillance</li>
      <li>Remote Automation</li>
    </ul>
    <div class="address-band">Kallang Way Link Hub #05-12 (Block B), Singapore 349201</div>
  </section>

</body>
</html>
```